Kestrel Facilities Business Card Design

We would now like to design business cards with the new Kestrel Facilities logo

Target Market(s)

Professional

Industry/Entity Type

Professional services

Contact Information for Business Card

Employee name, title, phone number, email address, corporate office address and logo.

Font styles to use
Sans Serif

Colors
0054AA
0677BA
7BADD7
CADEEF
E8F1F8

Requirements
Must have
• My logo
Should not have
• any other pictures or images besides my logo

```html
<!DOCTYPE html>
<html lang="en">
<head>
<meta charset="UTF-8">
<title>Kestrel Facilities Business Card</title>
<link href="https://fonts.googleapis.com/css2?family=Montserrat:wght@400;700&display=swap" rel="stylesheet">
<style>
  :root {
    --brand-blue: #3478c0;
    --paper: #ffffff;
    --ink: #1d1d1f;
    --backdrop: #d9d9d9;
  }
  * { margin: 0; padding: 0; box-sizing: border-box; }
  html, body { width: 1200px; height: 900px; overflow: hidden; }
  body {
    background: var(--backdrop);
    font-family: "Montserrat", sans-serif;
    position: relative;
  }
  .card {
    position: absolute;
    left: 330px;
    width: 540px;
    height: 310px;
    background: var(--paper);
    border-radius: 26px;
    overflow: hidden;
    box-shadow: 0 6px 18px rgba(0,0,0,0.15);
  }
  .card--back { top: 110px; }
  .card--front { top: 480px; }

  .wordmark {
    display: flex;
    align-items: center;
    gap: 12px;
    color: var(--brand-blue);
    font-weight: 700;
    line-height: 1.05;
    text-transform: uppercase;
  }
  .wordmark__square {
    width: 30px; height: 30px;
    background: var(--brand-blue);
    flex: none;
  }
  .card--back .wordmark {
    position: absolute;
    left: 50%; top: 50%;
    transform: translate(-50%, -50%);
    font-size: 34px;
  }
  .card--front .wordmark {
    position: absolute;
    right: 36px; top: 176px;
    font-size: 24px;
  }
  .card--front .wordmark__square { width: 24px; height: 24px; }

  .header-band {
    position: absolute;
    left: 0; top: 0;
    width: 100%; height: 128px;
    background: var(--brand-blue);
  }

  .holder {
    position: absolute;
    left: 32px; top: 40px;
    color: var(--paper);
  }
  .holder__name { font-size: 22px; font-weight: 700; letter-spacing: 0.5px; }
  .holder__title { font-size: 15px; font-weight: 400; margin-top: 4px; }

  .contact {
    position: absolute;
    left: 32px; top: 160px;
    color: var(--ink);
    font-size: 14px;
    line-height: 1.45;
  }
  .contact__address { margin-bottom: 12px; }
  .contact__row { display: flex; align-items: center; gap: 8px; }
  .contact__icon { width: 13px; height: 13px; flex: none; fill: var(--brand-blue); }
</style>
</head>
<body>

<section class="card card--back">
  <div class="wordmark"><span class="wordmark__square"></span><span>Kestrel<br>Facilities</span></div>
</section>

<section class="card card--front">
  <div class="header-band"></div>

  <div class="holder">
    <div class="holder__name">DANA WHITFIELD</div>
    <div class="holder__title">Co-Founder</div>
  </div>

  <div class="contact">
    <div class="contact__address">1840 N. Harbor Lane<br>Suite 410 Brookfield 27</div>
    <div class="contact__row">
      <svg class="contact__icon" viewBox="0 0 24 24"><path d="M6.6 10.8a15.1 15.1 0 0 0 6.6 6.6l2.2-2.2a1 1 0 0 1 1-.25 11.4 11.4 0 0 0 3.6.57 1 1 0 0 1 1 1V20a1 1 0 0 1-1 1A17 17 0 0 1 3 4a1 1 0 0 1 1-1h3.5a1 1 0 0 1 1 1c0 1.25.2 2.45.57 3.57a1 1 0 0 1-.25 1z"/></svg>
      <span>+254-300-41275</span>
    </div>
    <div class="contact__row">
      <svg class="contact__icon" viewBox="0 0 24 24"><path d="M2 5h20v14H2z M2 5l10 8 10-8" stroke="#fff" stroke-width="1.5"/></svg>
      <span>info@kestrelfacilities.com</span>
    </div>
    <div class="contact__row">
      <svg class="contact__icon" viewBox="0 0 24 24"><circle cx="12" cy="12" r="10"/><path d="M2 12h20M12 2c3 3 3 17 0 20M12 2c-3 3-3 17 0 20" stroke="#fff" stroke-width="1.3" fill="none"/></svg>
      <span>www.kestrelfacilities.com</span>
    </div>
  </div>

  <div class="wordmark"><span class="wordmark__square"></span><span>Kestrel<br>Facilities</span></div>
</section>

</body>
</html>
```